Podcast Cover Design - Dispatches Of Level Minds

We renamed our podcast from the "Marlow Home Trade Podcast" to "Dispatches Of Level Minds" and we need a new podcast cover design, Instagram profile picture, and a YouTube banner.

More so we're looking for some sort of symbol/icon. Our old logo had the Harlow Arch but we're moving to a much broader audience that isn't necessarily from Seattle and needs something that will appeal to them.

In the podcast, Dale reads the news that big media isn't covering including crime, business, homeless crisis, protests. We stay away from covering politics but our audience is mainly right-wing.

Attached are some additional designs we created in-house.

If we love the design we'll have additional job opportunities to create possible designs for merchandise.

Target Market(s)

80% Males aged 50+, Republican

Industry/Entity Type

News

Colors

Designer to choose colors to be used in the design.

Requirements
Must have
• OPEN TOO IDEAS
Nice to have
• OPEN TOO IDEAS
Should not have
• Harlow Arch

```html
<!DOCTYPE html>
<html lang="en">
<head>
<meta charset="utf-8">
<title>Dispatches Of Level Minds – Podcast Cover</title>
<link href="https://fonts.googleapis.com/css2?family=Anton&family=Montserrat:wght@800&display=swap" rel="stylesheet">
<style>
  :root {
    --red: #e21b26;
    --navy: #0a3349;
    --blue-deep: #0b4a6c;
    --blue-mid: #166a93;
    --cyan-glow: #3fc6e8;
    --white: #ffffff;
  }
  * { margin: 0; padding: 0; box-sizing: border-box; }
  html, body { width: 1200px; height: 1200px; overflow: hidden; background: var(--white); }
  .cover {
    position: relative;
    width: 1200px;
    height: 1200px;
    background: linear-gradient(180deg, var(--blue-deep) 0%, var(--blue-mid) 55%, var(--blue-deep) 100%);
    overflow: hidden;
  }
  .masthead { position: absolute; left: 0; top: 0; width: 1200px; height: 314px; display: block; }
  .masthead-title { font-family: 'Anton', sans-serif; font-size: 180px; fill: var(--white); }
  .masthead-connector { font-family: 'Montserrat', sans-serif; font-weight: 800; font-size: 96px; fill: var(--white); }
  .soundwave {
    position: absolute; left: 0; top: 640px; width: 1000px; height: 300px;
    background: radial-gradient(ellipse 55% 40% at 60% 50%, rgba(63,198,232,0.55) 0%, rgba(63,198,232,0.18) 45%, rgba(63,198,232,0) 75%);
  }
  .show-title {
    position: absolute; left: 82px; top: 322px;
    font-family: 'Anton', sans-serif;
    font-size: 200px; line-height: 0.98;
    color: var(--white);
    letter-spacing: 1px;
    text-transform: uppercase;
  }
  .host-photo {
    position: absolute; left: 560px; top: 540px; width: 640px; height: 483px;
    background: radial-gradient(ellipse 45% 60% at 52% 55%, #c99a85 0%, #8f6a5c 45%, rgba(90,60,70,0) 80%);
  }
  .host-with {
    position: absolute; left: 86px; top: 940px;
    font-family: 'Montserrat', sans-serif; font-weight: 800;
    font-size: 56px; color: var(--white); letter-spacing: 2px;
  }
  .host-band { position: absolute; left: 0; top: 1023px; width: 1200px; height: 177px; display: block; }
  .host-name { font-family: 'Montserrat', sans-serif; font-weight: 800; font-size: 84px; fill: var(--white); }
</style>
</head>
<body>
<main class="cover">
  <div class="soundwave" role="img" aria-label="Glowing cyan audio waveform graphic"></div>

  <svg class="masthead" viewBox="0 0 1200 314" xmlns="http://www.w3.org/2000/svg">
    <rect width="1200" height="314" fill="var(--red)"/>
    <rect x="960" y="0" width="240" height="314" fill="var(--navy)"/>
    <text class="masthead-title" x="70" y="245" textLength="820" lengthAdjust="spacingAndGlyphs">DISPATCHES</text>
    <text class="masthead-connector" x="1080" y="192" text-anchor="middle">OF</text>
  </svg>

  <h1 class="show-title">Level<br>Minds</h1>

  <div class="host-photo" role="img" aria-label="Portrait photo of host Dale in a checked shirt beside a vintage microphone"></div>

  <p class="host-with">WITH</p>

  <svg class="host-band" viewBox="0 0 1200 177" xmlns="http://www.w3.org/2000/svg">
    <rect width="1200" height="177" fill="var(--red)"/>
    <polygon points="1148,0 1200,0 1200,177 1055,177" fill="var(--navy)"/>
    <polygon points="1168,0 1186,0 1093,177 1075,177" fill="var(--red)"/>
    <polygon points="1196,0 1200,0 1200,40 1125,177 1107,177" fill="var(--red)"/>
    <text class="host-name" x="82" y="118" textLength="930" lengthAdjust="spacingAndGlyphs">DALE WHITCOMBE</text>
  </svg>
</main>
</body>
</html>
```